Home Security Company Business Card

Looking for a eye catching business card that is non traditional and stands out but yet still looks professional. It should include all the pertinent information such as name, title, address, telephone, e-mail, website address should definitely stand out and then finally the logo.

Target Market(s)

Residential and Commercial accounts mostly upscale accounts

Industry/Entity Type

Security

Contact Information for Business Card

Name
Title
Address
Office #
Cell #
E-mail
Website

Font styles to use
Serif
Sans Serif

Requirements
Must have
• Logo, two sided color configuration
Nice to have
• You decide
Should not have
• There really aren't any.

```html
<!DOCTYPE html>
<html lang="en">
<head>
<meta charset="utf-8">
<title>Harborline Security Systems – Business Card</title>
<link href="https://fonts.googleapis.com/css2?family=Open+Sans:wght@400;600;700&display=swap" rel="stylesheet">
<style>
  :root {
    --maroon: #7a1418;
    --maroon-deep: #5c0c10;
    --maroon-light: #a3262c;
    --gold: #e2a93b;
    --paper: #ffffff;
    --stage: #ece8e3;
    --ink-white: #ffffff;
  }
  * { box-sizing: border-box; margin: 0; padding: 0; }
  html, body { width: 1200px; height: 913px; overflow: hidden; }
  body {
    background: var(--stage);
    font-family: "Open Sans", Arial, sans-serif;
    display: flex;
    align-items: center;
    justify-content: center;
    gap: 40px;
  }
  .card {
    position: relative;
    width: 540px;
    height: 309px;
    border-radius: 4px;
    overflow: hidden;
    box-shadow: 0 8px 24px rgba(0,0,0,0.18);
  }
  /* Front */
  .card-front { background: var(--paper); }
  .brand {
    position: absolute;
    display: flex;
    align-items: center;
    gap: 10px;
    font-weight: 700;
    letter-spacing: 0.04em;
    line-height: 1.15;
  }
  .brand-dot {
    width: 34px; height: 34px; border-radius: 50%;
    background: var(--gold);
    flex: none;
  }
  .card-front .brand { top: 50px; left: 250px; color: var(--maroon); font-size: 15px; }
  .contacts {
    position: absolute;
    right: 36px; top: 100px;
    list-style: none;
    text-align: right;
    color: var(--maroon);
    font-size: 12.5px;
    font-weight: 600;
    line-height: 19px;
  }
  .contacts li { display: flex; justify-content: flex-end; align-items: center; gap: 8px; }
  .contacts svg { width: 11px; height: 11px; fill: none; stroke: var(--gold); stroke-width: 1.6; }
  .holder { position: absolute; left: 40px; right: 36px; top: 158px; }
  .holder-row { display: flex; align-items: flex-end; gap: 12px; }
  .holder-name { color: var(--maroon); font-size: 22px; font-weight: 700; line-height: 30px; white-space: nowrap; flex: none; }
  .holder-rule { flex: 1; height: 1.5px; background: var(--maroon); margin-bottom: 6px; }
  .holder-title { color: var(--gold); font-size: 13px; font-weight: 600; line-height: 18px; }
  .accent-half {
    position: absolute; left: -22px; top: 196px;
    width: 44px; height: 44px; border-radius: 50%;
    background: var(--gold);
  }
  .address {
    position: absolute; left: 40px; top: 232px;
    color: var(--maroon); font-size: 14px; font-weight: 600; line-height: 20px;
    font-style: normal;
  }
  /* Back */
  .card-back {
    background: radial-gradient(ellipse at 70% 20%, var(--maroon-light), var(--maroon) 55%, var(--maroon-deep));
  }
  .card-back .brand { top: 92px; left: 50%; transform: translateX(-50%); color: var(--ink-white); font-size: 17px; white-space: nowrap; }
  .rule-back {
    position: absolute; left: 60px; right: 60px; top: 178px;
    height: 1.5px; background: var(--gold);
  }
  .website {
    position: absolute; left: 0; right: 0; top: 196px;
    text-align: center; color: var(--ink-white);
    font-size: 15px; font-weight: 600; letter-spacing: 0.02em;
  }
</style>
</head>
<body>
  <section class="card card-front" aria-label="Business card front">
    <div class="brand"><span class="brand-dot"></span><span>HARBORLINE<br>SECURITY SYSTEMS INC.</span></div>
    <ul class="contacts">
      <li>+330 2718-4052
        <svg viewBox="0 0 12 12"><rect x="1.5" y="3" width="9" height="7" rx="1"/><path d="M3 3 V1.5 H9 V3"/></svg></li>
      <li>+3302615-47381
        <svg viewBox="0 0 12 12"><path d="M2 1.5 L4.5 1.5 L5.5 4 L4 5 Q5 7.5 7 8 L8 6.5 L10.5 7.5 L10.5 10 Q4 10.5 2 1.5 Z"/></svg></li>
      <li>info@markdelaneymail.com
        <svg viewBox="0 0 12 12"><rect x="1" y="2.5" width="10" height="7" rx="0.5"/><path d="M1 2.5 L6 6.5 L11 2.5"/></svg></li>
    </ul>
    <div class="holder">
      <div class="holder-row">
        <div class="holder-name">Mark Delaney</div>
        <div class="holder-rule"></div>
      </div>
      <div class="holder-title">Owner</div>
    </div>
    <div class="accent-half"></div>
    <address class="address">742 Lantern Avenue<br>Dalton, Illinois 60147</address>
  </section>

  <section class="card card-back" aria-label="Business card back">
    <div class="brand"><span class="brand-dot"></span><span>HARBORLINE<br>SECURITY SYSTEMS INC.</span></div>
    <div class="rule-back"></div>
    <div class="website">www.harborlinesecuritysystems.com</div>
  </section>
</body>
</html>
```